Berufora Banner Design (Profilbanner und Unternehmensbanner) (1584 x 396) (1128 x 191)
Zielgruppe
Ich bin Dienstleister und Unternehmensberater für technischen B2B Vertrieb.
Für meinen BeruFora Account suche ich einen Banner für meine Profilseite und einen Banner für die Unternehmensseite). Meine Zielgruppe sind leitende Angestellte in Unternehmen. Das Design sollte entsprechend grafisch hochwertig, seriös gestaltet sein.
I am a service provider and management consultant for technical B2B sales.
For my BeruFora account, I'm looking for a banner for my profile page and a banner for the company page). My target group are executives in companies. The design should have a correspondingly high-quality graphic design and be serious.
Aufgabenstellung
Wichtig ist die Berücksichtigung meines Logos (PNG im Anhang) und des Corporate Identity Farben (PDF Anhang und unten stehend). Stock Bilder oder Grafiken können/sollen gerne mit eingebunden werden. Wichtig ist hier der passende Gesamteindruck.
It is important to consider my logo (PNG in the attachment) and the corporate identity colors (PDF attachment and below). Stock images or graphics can/should be included. The right overall impression is important here.
HEX / HTML 002854
HEX / HTML 00b6e3
Bannergrößen / Banner sizes
Profilbanner (1584 x 396)
Unternehmensseitenbanner (1128 x 191)

```html
<!DOCTYPE html>
<html lang="de">
<head>
<meta charset="utf-8">
<title>Lorenz Wegmeier Management &amp; Sales Consulting – Unternehmensseite</title>
<link rel="stylesheet" href="https://fonts.googleapis.com/css2?family=Titillium+Web:wght@300;400;700&family=Open+Sans:wght@400;500;600&display=swap">
<style>
  :root {
    --banner-light: #12a6f0;
    --banner-mid: #0a6ee0;
    --banner-deep: #0a33b8;
    --engine-dark: #1a1d26;
    --engine-mid: #6c7486;
    --logo-navy: #14284a;
    --logo-cyan: #1fb4e6;
    --white: #ffffff;
    --ink: #1d1d1d;
    --ink-soft: #3a3a3a;
    --muted: #666666;
    --action: #0a66c2;
    --border: #7a7a7a;
    --rule: #e6e6e6;
  }
  * { box-sizing: border-box; margin: 0; padding: 0; }
  html, body { width: 1200px; height: 656px; overflow: hidden; background: var(--white); }
  .page { position: relative; width: 1200px; height: 656px; font-family: "Open Sans", sans-serif; }

  .banner {
    position: absolute; left: 0; top: 0; width: 1200px; height: 299px; overflow: hidden;
    background: linear-gradient(100deg, var(--banner-light) 0%, var(--banner-mid) 40%, var(--banner-deep) 75%);
  }
  .engine-visual {
    position: absolute; left: 709px; top: 0; width: 491px; height: 299px;
    background: radial-gradient(ellipse at 45% 55%, var(--engine-mid) 0%, #3a404e 35%, var(--engine-dark) 70%, rgba(26,29,38,0) 100%);
  }
  .headline {
    position: absolute; font-family: "Titillium Web", sans-serif; color: var(--white);
    font-size: 40px; line-height: 1; letter-spacing: 0.3px; white-space: nowrap;
  }
  .headline .light { font-weight: 300; }
  .headline .bold { font-weight: 700; }
  .headline-one { left: 200px; top: 72px; }
  .headline-two { left: 238px; top: 125px; }

  .contact {
    position: absolute; top: 249px; display: flex; align-items: center; gap: 8px;
    font-family: "Titillium Web", sans-serif; font-size: 15px; font-weight: 400; color: var(--white);
    letter-spacing: 0.3px; white-space: nowrap;
  }
  .contact-phone { left: 238px; }
  .contact-web { left: 405px; }
  .contact svg { width: 24px; height: 24px; }

  .brand-tile {
    position: absolute; left: 38px; top: 209px; width: 167px; height: 165px;
    background: var(--logo-navy); display: flex; align-items: center; justify-content: center;
    text-align: center; padding: 14px;
    font-family: "Titillium Web", sans-serif; font-weight: 700; font-size: 22px; line-height: 1.15; color: var(--logo-cyan);
  }

  .company-name { position: absolute; left: 35px; top: 394px; font-size: 35px; line-height: 48px; font-weight: 600; color: var(--ink); white-space: nowrap; }
  .company-tagline { position: absolute; left: 35px; top: 442px; font-size: 22px; line-height: 30px; color: var(--ink-soft); white-space: nowrap; }
  .company-meta { position: absolute; left: 34px; top: 475px; font-size: 19.5px; line-height: 27px; color: var(--muted); white-space: nowrap; }
  .company-staff { position: absolute; left: 35px; top: 520px; font-size: 22px; line-height: 30px; font-weight: 500; color: var(--muted); white-space: nowrap; }

  .action {
    position: absolute; top: 579px; height: 49px; border-radius: 25px;
    display: flex; align-items: center; justify-content: center; gap: 8px;
    font-size: 22px; font-weight: 600; white-space: nowrap;
  }
  .action-follow { left: 35px; width: 210px; background: var(--action); color: var(--white); }
  .action-website { left: 258px; width: 292px; border: 2px solid var(--action); color: var(--action); }
  .action-more { left: 563px; width: 110px; border: 2px solid var(--border); color: var(--muted); font-weight: 400; }
  .action svg { width: 20px; height: 20px; }

  .page-rule { position: absolute; left: 0; top: 651px; width: 1200px; height: 2px; background: var(--rule); }
</style>
</head>
<body>
<div class="page">
  <header class="banner">
    <div class="engine-visual" role="img" aria-label="Foto eines Automotors mit Riemenscheiben und Ansaugkrümmer"></div>
    <div class="headline headline-one"><span class="light">VOLLE </span><span class="bold">POWER</span></div>
    <div class="headline headline-two"><span class="light">FÜR IHR </span><span class="bold">BUSINESS</span><span class="light">.</span></div>
    <div class="contact contact-phone">
      <svg viewBox="0 0 24 24" fill="none" stroke="currentColor" stroke-width="1.6" stroke-linejoin="round"><path d="M5 3h4l2 5-2.5 1.5a11 11 0 0 0 6 6L16 13l5 2v4a2 2 0 0 1-2 2A16 16 0 0 1 3 5a2 2 0 0 1 2-2z"/></svg>
      <span>0234 | 567 891 0</span>
    </div>
    <div class="contact contact-web">
      <svg viewBox="0 0 24 24" fill="none" stroke="currentColor" stroke-width="1.5"><circle cx="12" cy="12" r="9.5"/><ellipse cx="12" cy="12" rx="4.2" ry="9.5"/><path d="M2.5 12h19M4 7h16M4 17h16"/></svg>
      <span>LORENZWEGMEIER.DE</span>
    </div>
  </header>

  <div class="brand-tile">Lorenz Wegmeier</div>

  <h1 class="company-name">Lorenz Wegmeier Management &amp; Sales Consulting GmbH</h1>
  <p class="company-tagline">B2B Sales Consulting</p>
  <p class="company-meta">Business Consulting und Unternehmensdienstleistungen · Bad Lindenau, North Rhine-Westphalia · 1 Follower</p>
  <p class="company-staff">1 Mitarbeiter:in auf BeruFora ansehen</p>

  <div class="action action-follow">
    <svg viewBox="0 0 20 20" stroke="currentColor" stroke-width="2.6" stroke-linecap="round"><path d="M10 2v16M2 10h16"/></svg>
    <span>Folgen</span>
  </div>
  <div class="action action-website">
    <span>Website besuchen</span>
    <svg viewBox="0 0 20 20" fill="none" stroke="currentColor" stroke-width="2.2" stroke-linecap="round" stroke-linejoin="round"><path d="M9 4H4v12h12v-5M12 2h6v6M18 2l-8 8"/></svg>
  </div>
  <div class="action action-more"><span>Mehr</span></div>

  <div class="page-rule"></div>
</div>
</body>
</html>
```